RM Installations Web Site Design

Need a basic site to show clients a little about what we do. We are a custom audio video company in the high-end residential market. Need a few basic but professional pages to show past projects and products we sell. No e-commerce. Should include my new logo from MarkBazaar.

Industry/Entity Type

Residential

Number of Pages Required

2 page

Font styles to use
Serif
Sans Serif

Colors
f78f20

Requirements
Must have
• Company Logo, Send feedback page
Nice to have
• I have no ideas about design, but I do know what I like and dislike when I see it.

```html
<!DOCTYPE html>
<html lang="en">
<head>
<meta charset="utf-8">
<title>RM Installations</title>
<link href="https://fonts.googleapis.com/css2?family=Lato:wght@300;400;700&display=swap" rel="stylesheet">
<style>
:root{
  --orange:#f78f20;
  --ink:#2b2b2b;
  --nav:#1c1c1c;
  --band:#ebebeb;
  --slate:#666666;
  --footer:#232323;
  --base:#141414;
  --muted:#8a8a8a;
}
*{box-sizing:border-box;margin:0;padding:0}
html,body{width:674px;height:1200px;overflow:hidden;background:#fff}
body{position:relative;font-family:'Lato',sans-serif;color:var(--ink)}
.abs{position:absolute}
.header{left:0;top:0;width:674px;height:30px;background:#fff}
.brand{left:70px;top:0;width:168px;height:53px;background:#fff;z-index:3;display:flex;align-items:center;gap:8px;padding-left:10px;box-shadow:0 1px 3px rgba(0,0,0,.15)}
.brand-mark{width:26px;height:26px;background:var(--orange)}
.brand-name{font-size:15px;font-weight:400;color:var(--ink);line-height:1.05;letter-spacing:.3px}
.feedback-btn{left:422px;top:5px;width:52px;height:16px;border:1px solid var(--orange);font-size:6.5px;font-weight:700;display:flex;align-items:center;justify-content:center;letter-spacing:.3px}
.call{left:504px;top:3px;display:flex;gap:5px;align-items:center}
.call-icon{width:21px;height:21px;border:1.5px solid var(--orange);border-radius:50%;display:flex;align-items:center;justify-content:center}
.call-label{font-size:7.5px;letter-spacing:1.5px;line-height:1}
.call-number{font-size:11px;font-weight:400;line-height:1.2;letter-spacing:.5px}
.nav{left:0;top:30px;width:674px;height:28px;background:var(--nav)}
.nav a{position:absolute;top:0;height:28px;display:flex;align-items:center;justify-content:center;color:#fff;font-size:8.5px;font-weight:700;text-decoration:none;border-right:1px solid #444}
.nav a.active{background:var(--orange);font-weight:400}
.hero{left:0;top:58px;width:674px;height:236px;overflow:hidden}
.hero-photo{position:absolute;inset:0;background:
  radial-gradient(ellipse 90px 70px at 200px 120px,rgba(40,60,70,.55),rgba(40,60,70,0)),
  radial-gradient(ellipse 120px 110px at 60px 140px,rgba(70,100,140,.8),rgba(70,100,140,0)),
  linear-gradient(100deg,#5c7d9c 0%,#8fa4b8 30%,#c9ccd0 55%,#e8e8e8 100%)}
.hero-panel{position:absolute;left:0;top:0}
.hero-title{position:absolute;right:81px;top:46px;text-align:right;font-size:29px;font-weight:300;line-height:35px;color:#2a2a2a}
.shadow{height:10px;background:radial-gradient(ellipse at top,rgba(0,0,0,.28),rgba(0,0,0,0) 70%)}
.title{width:674px;text-align:center;font-size:24px;font-weight:400;letter-spacing:.3px}
.title .hl{color:var(--orange)}
.divider{left:0;width:674px;height:8px}
.divider .line{position:absolute;top:3px;height:1px;background:#9a9a9a;width:81px}
.divider .dot{position:absolute;left:332px;top:0;width:9px;height:9px;border-radius:50%;background:var(--orange)}
.intro{left:140px;top:386px;width:394px;text-align:center;font-size:7.6px;line-height:13.5px;color:#333}
.more-btn{left:311px;top:435px;width:51px;height:15px;border:1px solid var(--orange);border-radius:2px;font-size:6px;font-weight:700;display:flex;align-items:center;justify-content:center}
.services{left:0;top:478px;width:674px;height:220px;background:var(--band)}
.service{position:absolute;top:75px;width:110px;text-align:center}
.service-icon{width:64px;height:64px;border-radius:50%;margin:0 auto;border:3px solid #fff;box-shadow:0 0 0 1px #ddd;background:#111;display:flex;align-items:center;justify-content:center}
.service-icon.on{background:var(--orange)}
.service h3{font-size:9.4px;font-weight:700;line-height:11px;margin-top:10px;color:#333}
.service p{font-size:7.2px;line-height:10.5px;margin:7px auto 0;width:96px;color:#555}
.sep{position:absolute;top:88px;width:1px;height:110px;background:#dadada}
.arrow{position:absolute}
.projects{left:0;top:721px;width:674px;height:199px;background:var(--slate)}
.project{position:absolute;top:82px;width:122px;height:80px;border:3px solid #fff;box-shadow:0 3px 5px rgba(0,0,0,.35)}
.contact-field{position:absolute;border:1px solid #555;border-radius:2px;font-size:6.5px;color:#aaa;padding:5px 12px}
.submit{left:513px;top:1052px;width:51px;height:16px;border:1px solid var(--orange);border-radius:2px;font-size:8px;font-weight:700;display:flex;align-items:center;justify-content:center}
.footer{left:0;top:1094px;width:674px;height:79px;background:var(--footer);color:#ddd}
.footer-links{position:absolute;left:141px;top:10px;display:flex;font-size:7.6px}
.footer-links span{border-left:1px solid #aaa;padding:0 13px;line-height:9px}
.footer-links span:last-child{border-right:1px solid #aaa}
.footer-links .active{color:var(--orange)}
.footer-info{position:absolute;font-size:7px;line-height:9px;display:flex;gap:5px}
.social{position:absolute;left:376px;top:51px;display:flex;gap:7px}
.social i{display:block;width:13px;height:13px;background:#ddd}
.social i.on{background:var(--orange)}
.footer-brand{position:absolute;left:480px;top:33px;display:flex;align-items:center;gap:6px}
.footer-brand .brand-mark{width:22px;height:22px;background:#777}
.footer-brand span{font-size:11px;color:#8d8d8d;line-height:1.05}
.base{left:0;top:1173px;width:674px;height:27px;background:var(--base);color:#ccc;font-size:7px;display:flex;align-items:center;justify-content:center}
</style>
</head>
<body>

<div class="abs header"></div>
<div class="abs brand"><div class="brand-mark"></div><div class="brand-name">RM<br>INSTALLATIONS</div></div>
<div class="abs feedback-btn">FEEDBACK</div>
<div class="abs call">
  <div class="call-icon"><svg width="11" height="11" viewBox="0 0 24 24"><path d="M6.6 10.8a15 15 0 0 0 6.6 6.6l2.2-2.2c.3-.3.7-.4 1-.2 1.1.4 2.3.6 3.6.6.6 0 1 .4 1 1V20c0 .6-.4 1-1 1A17 17 0 0 1 3 4c0-.6.4-1 1-1h3.5c.6 0 1 .4 1 1 0 1.3.2 2.5.6 3.6.1.3 0 .7-.2 1z" fill="#f78f20"/></svg></div>
  <div><div class="call-label">CALL US TODAY</div><div class="call-number">012-345-6789</div></div>
</div>

<nav class="abs nav">
  <a class="active" style="left:251px;width:45px">HOME</a>
  <a style="left:296px;width:62px">ABOUT US</a>
  <a style="left:358px;width:96px">Product &amp; Services</a>
  <a style="left:454px;width:73px">Past Projects</a>
  <a style="left:527px;width:73px">CONTACT US</a>
</nav>

<section class="abs hero">
  <div class="hero-photo" role="img" aria-label="Photo of a technician drilling a wall mount for an installation"></div>
  <svg class="hero-panel" width="674" height="236" viewBox="0 0 674 236">
    <defs><linearGradient id="panelFade" x1="1" y1="0" x2="0" y2="0.4"><stop offset="0" stop-color="#f9a66a"/><stop offset="0.55" stop-color="#fcd9c2"/><stop offset="1" stop-color="#fff4ec"/></linearGradient></defs>
    <polygon points="372,0 674,0 674,236 448,236" fill="url(#panelFade)"/>
  </svg>
  <h1 class="hero-title">We Are<br>Custom<br>Audio Video<br>Company</h1>
</section>
<div class="abs shadow" style="left:100px;top:294px;width:480px"></div>

<div class="abs title" style="top:317px;font-size:16px;color:var(--orange);line-height:20px">WELCOME TO</div>
<div class="abs title" style="top:334px;line-height:30px">RM INSTALLATIONS</div>
<div class="abs divider" style="top:366px"><div class="line" style="left:233px"></div><div class="dot"></div><div class="line" style="left:360px"></div></div>
<p class="abs intro">Lorem Ipsum Dolor Sit Amet, Consectetur Adipiscing Elit. Aenean Sodales Diam Quis Velit Pellentesque Vehicula. Donec Luctus Justo Aliquet Est Volutpat, Sedtincidunt Odio Pretium. Sed Id Est Ultrici Rutrum Arcu Pretium, Porttitor Enim. Integer Quis Luctus Ligula. Donec Id Scelerisque Lorem.</p>
<div class="abs more-btn">READ MORE »</div>

<section class="abs services">
  <div class="abs title" style="top:20px;line-height:30px"><span class="hl">OUR</span> SERVICES</div>
  <div class="abs divider" style="top:52px"><div class="line" style="left:287px;width:40px"></div><div class="dot"></div><div class="line" style="left:347px;width:40px"></div></div>
  <svg class="arrow" style="left:29px;top:131px" width="12" height="18"><path d="M10 1 2 9l8 8" stroke="#444" stroke-width="1.6" fill="none"/></svg>
  <svg class="arrow" style="left:633px;top:131px" width="12" height="18"><path d="M2 1l8 8-8 8" stroke="#444" stroke-width="1.6" fill="none"/></svg>

  <div class="service" style="left:62px"><div class="service-icon on">
    <svg width="34" height="34" viewBox="0 0 34 34" fill="none" stroke="#fff" stroke-width="1.8" stroke-linejoin="round" role="img" aria-label="Video screen icon"><path d="M8 14a5 5 0 0 1 9-3 4 4 0 0 1 6 3.5H8z"/><rect x="7" y="17" width="20" height="12" rx="1"/><path d="M15 20v6l5-3z" fill="#fff"/><path d="M4 31h26"/></svg>
  </div><h3>Distributed<br>Video</h3><p>Lorem ipsum dolor si amet consectetur adipiscing elit Etiam feugiat urna leo</p></div>
  <div class="sep" style="left:171px"></div>

  <div class="service" style="left:171px"><div class="service-icon">
    <svg width="34" height="34" viewBox="0 0 34 34" fill="none" stroke="#fff" stroke-width="1.8" stroke-linejoin="round" role="img" aria-label="Media equipment icon"><rect x="5" y="5" width="13" height="22" rx="1"/><circle cx="9" cy="9" r="1.3" fill="#fff"/><circle cx="14" cy="9" r="1.3" fill="#fff"/><path d="M8 14h7M8 18h7M8 22h7"/><rect x="15" y="15" width="15" height="11" rx="1" fill="#111"/><path d="M20 29h5M22.5 26v3"/></svg>
  </div><h3>Media<br>Rooms</h3><p>Lorem ipsum dolor si amet consectetur adipiscing elit Etiam feugiat urna leo</p></div>
  <div class="sep" style="left:281px"></div>

  <div class="service" style="left:282px"><div class="service-icon">
    <svg width="34" height="34" viewBox="0 0 34 34" fill="none" stroke="#fff" stroke-width="1.8" stroke-linejoin="round" role="img" aria-label="Cinema screen icon"><rect x="6" y="4" width="22" height="16" rx="1"/><circle cx="17" cy="12" r="4.5"/><path d="M15.5 9.8v4.4l3.6-2.2z" fill="#fff"/><path d="M5 30v-5h24v5z" fill="#fff"/><path d="M11 25v5M17 25v5M23 25v5" stroke="#111"/></svg>
  </div><h3>Residential<br>Cinemas</h3><p>Lorem ipsum dolor si amet consectetur adipiscing elit Etiam feugiat urna leo</p></div>
  <div class="sep" style="left:391px"></div>

  <div class="service" style="left:391px"><div class="service-icon">
    <svg width="34" height="34" viewBox="0 0 34 34" fill="none" stroke="#fff" stroke-width="1.8" stroke-linejoin="round" role="img" aria-label="House with tools icon"><path d="M12 16 21 7l10 9" /><path d="M15 14v14h13V14" fill="#fff"/><rect x="19" y="20" width="5" height="8" fill="#111" stroke="none"/><path d="M4 28 14 18M5 17l9 11" stroke-width="2.2"/></svg>
  </div><h3>Whole-House<br>Control Systems</h3><p>Lorem ipsum dolor si amet consectetur adipiscing elit Etiam feugiat urna leo</p></div>
  <div class="sep" style="left:501px"></div>

  <div class="service" style="left:502px"><div class="service-icon">
    <svg width="34" height="34" viewBox="0 0 34 34" fill="none" stroke="#fff" stroke-width="1.8" stroke-linecap="round" role="img" aria-label="Plug and light icon"><path d="M9 4v5M13 4v5"/><rect x="7.5" y="9" width="7" height="5" rx="1" fill="#fff"/><path d="M11 14v6c0 3 2 4 5 4"/><circle cx="21" cy="22" r="5" fill="#fff"/><path d="M21 13v2M21 29v2M12 22h2M28 22h2M15 16l1.4 1.4M25.6 26.6 27 28M27 16l-1.4 1.4"/></svg>
  </div><h3>Automated<br>Lighting Control</h3><p>Lorem ipsum dolor si amet consectetur adipiscing elit Etiam feugiat urna leo</p></div>
</section>
<div class="abs shadow" style="left:70px;top:698px;width:534px"></div>

<section class="abs projects">
  <div class="abs title" style="top:18px;line-height:30px;color:#ccc"><span class="hl">PAST</span> PROJECTS</div>
  <div class="abs divider" style="top:51px"><div class="line" style="left:248px;width:70px;background:#bbb"></div><div class="dot"></div><div class="line" style="left:343px;width:70px;background:#bbb"></div></div>
  <svg class="arrow" style="left:48px;top:112px" width="10" height="16"><path d="M8 1 2 8l6 7" stroke="#fff" stroke-width="1.6" fill="none"/></svg>
  <svg class="arrow" style="left:616px;top:112px" width="10" height="16"><path d="M2 1l6 7-6 7" stroke="#fff" stroke-width="1.6" fill="none"/></svg>
  <div class="project" style="left:74px;background:linear-gradient(180deg,#1e2c4a 0%,#3e5a86 22%,#2a2d3a 35%,#6b3a26 55%,#a0532e 75%,#6a3320 100%)" role="img" aria-label="Photo of a restaurant bar with wall-mounted screens"></div>
  <div class="project" style="left:209px;background:radial-gradient(ellipse 22px 14px at 50% 32%,#e6e2da 60%,rgba(230,226,218,0) 62%),linear-gradient(180deg,#9a2c1e 0%,#7a2418 45%,#3c2e28 70%,#2a2420 100%)" role="img" aria-label="Photo of a home cinema room with recliners"></div>
  <div class="project" style="left:343px;background:linear-gradient(90deg,#ddd6cc 0%,#e6cdb6 22%,#c8392c 38%,#b8302a 48%,#ece9e4 62%,#dfe2e4 100%)" role="img" aria-label="Photo of a homeowner using a wall touch panel"></div>
  <div class="project" style="left:478px;background:radial-gradient(ellipse 40px 26px at 45% 50%,#7a4a38,rgba(122,74,56,0) 80%),linear-gradient(135deg,#0c0c0c 0%,#2a1e1a 45%,#d8c2b0 80%,#1a1a1a 100%)" role="img" aria-label="Photo of a hand tapping a control touchscreen"></div>
</section>
<div class="abs shadow" style="left:70px;top:920px;width:534px"></div>

<div class="abs title" style="top:940px;line-height:30px"><span class="hl">QUICK</span> CONTACT</div>
<div class="abs divider" style="top:972px"><div class="line" style="left:248px;width:70px"></div><div class="dot"></div><div class="line" style="left:343px;width:70px"></div></div>
<div class="contact-field" style="left:74px;top:999px;width:169px;height:19px">Name</div>
<div class="contact-field" style="left:252px;top:999px;width:170px;height:19px">Mob</div>
<div class="contact-field" style="left:430px;top:999px;width:170px;height:19px">Email</div>
<div class="contact-field" style="left:74px;top:1024px;width:432px;height:44px">Message</div>
<div class="abs submit">SUBMIT</div>

<footer class="abs footer">
  <div class="footer-links"><span class="active">Home</span><span>About Us</span><span>Product &amp; Services</span><span>Past Projects</span><span>Feedback</span><span>Contact Us</span></div>
  <div class="footer-info" style="left:73px;top:38px"><svg width="7" height="9" viewBox="0 0 10 14"><path d="M5 0a5 5 0 0 0-5 5c0 4 5 9 5 9s5-5 5-9a5 5 0 0 0-5-5zm0 7a2 2 0 1 1 0-4 2 2 0 0 1 0 4z" fill="#fff"/></svg><div>Lorem Ipsum,<br>Dolor sit amet consectetuer,<br>Adipiscing - 12345</div></div>
  <div class="footer-info" style="left:210px;top:38px"><svg width="8" height="8" viewBox="0 0 24 24"><path d="M6.6 10.8a15 15 0 0 0 6.6 6.6l2.2-2.2c.3-.3.7-.4 1-.2 1.1.4 2.3.6 3.6.6.6 0 1 .4 1 1V20c0 .6-.4 1-1 1A17 17 0 0 1 3 4c0-.6.4-1 1-1h3.5c.6 0 1 .4 1 1 0 1.3.2 2.5.6 3.6.1.3 0 .7-.2 1z" fill="#fff"/></svg><div>Phone: 0123 456 789</div></div>
  <div class="footer-info" style="left:210px;top:55px"><svg width="10" height="8" viewBox="0 0 20 14"><rect x="0.5" y="0.5" width="19" height="13" fill="none" stroke="#fff"/><path d="M1 1l9 7 9-7" stroke="#fff" fill="none"/></svg><div>info@rminstallations.com</div></div>
  <div class="social"><i class="on"></i><i></i><i></i><i></i></div>
  <div class="footer-brand"><div class="brand-mark"></div><span>RM<br>INSTALLATIONS</span></div>
</footer>
<div class="abs base">© 2015 RMInstallationsAudioVideoControl &nbsp;|&nbsp; All rights reserved</div>

</body>
</html>
```